Website Design for a Luxury Wedding & Events Company

We are launching a British luxury wedding & event planning consultancy business providing bespoke, elegant and first-class service to our discerning clients in the UK and abroad. We specialize in Weddings (which will have it's on page) however we also provide service for other occasion which will be included in a single page 'Events'.

We require a company website design befitting of our luxury brand. Once designed we will post another job to code the website so that it can be hosted by HostPlume.com.

The website has to set the tone for our business and type of premium service we provide. Our website design has to be BESPOKE and have a luxury and elegant look and feel about it.

PLEASE REFER TO THE IMAGES ATTACHED TO GET AN UNDERSTANDING OF THE DESIGN CONCEPT WE WANT. ALL DESIGNS SUBMITTED MUST FOLLOW THE CONCEPT SPECIFIED!!!

We appreciate that the current budget will not permit for the design of all pages referenced above, so we are happy to have designs for up to 3 pages initially; Landing page (we have attached an examples of what we want), 'Home' page (an example is also attached) and 'About' us page. When we are happy with a particular design we can add payment for remainder of the pages required.

The final website design will have the following pages:
1a) URL Landing Page (details below)
1b) Home
2) About
3) Luxury Weddings
4) Services (this can either be a separate tab or linked to 'Luxury Weddings' - however it does need to be a separate page)
subheadings are:
> Comprehensive Wedding Planning Service
> Wedding Day Coordination Service
> Consultancy Service
5) Events
6) Gallery
7) Testimonials
8) Contact

We have a concept of the website is as follows:
URL Landing Page:
Option 1: This should just be simple but makes an immediate statement.
We have attached an image of how this could potentially look. The logo featured in the photo example needs to be replaced with our logo (reference site: http://tesslovank.com/).

Option 2: Alternatively this could be an actually door in the middle of the page - Imagine the big black gloss door at Number 14 Corwell Terrace (London Prime Minister's home).

By clicking the door knocker on either options , the 'Home Page' will be opened.

Our tag line should also be tastefully integrated:
'Exclusive Events, Masterfully Produced, Distinctively Designed'

The 'HOME PAGE' - should look like a luxury boutique office or reception lounge (luxury table, luxury head chair and luxury 2 client chairs; elegant chandelier, beautiful flowers on the table, 2 flutes of champagne on the table; and filing cabinets with drawers that are labelled with different website pages, e.g. 'about us', 'services', 'gallery', etc. By clicking on the drawers the details behind that page will open up in a separate tab/page.)

Our tag line should be on the Home Page also.

The overall concept and look and feel of website is all about taking people on a journey and giving them a glimpse of the luxury service that awaits them.

Colours: We want the general look and feel of the website to be WHITE, or OFF-WHITE with soft hints of gold to match the logo (tab/page headings could be gold). The only dark page should be the URL Landing page (ref to website images attached).

The website and images need to be compatible with mobile devices, smartphones, Tabros, etc. In terms of fit to screen, resolution etc...

We require links to our Pagewall, Quillet, Snapvuely and Boardlyne Pages (links to be provided later)

This is the rough concept and looking for designers to try to elevate this vision. :-) We are open for designers to interpret this concept in their own way.

Website wording/content is all ready to go...

We have attached our logo, and some imagery to help...

Target Market(s)

Luxury Wedding & Events Market

Industry/Entity Type

Wedding Planner

Number of Pages Required

3 page

Font styles to use
Sans Serif

Colors
ffffff

Requirements
Must have
• Tag Line:
• 'Exquisite Events, Masterfully Produced, Distinctively Designed'

```html
<!DOCTYPE html>
<html lang="en">
<head>
<meta charset="utf-8">
<title>Elena Marlowe — Luxury Wedding &amp; Event Consultants</title>
<link href="https://fonts.googleapis.com/css2?family=Cinzel:wght@400&family=Open+Sans:wght@600&display=swap" rel="stylesheet">
<style>
  :root {
    --bg: #111111;
    --gold: #d6b768;
    --ornament: #2b2b2b;
    --button-top: #5a5a5a;
    --button-bottom: #2e2e2e;
    --button-frame: #1c1c1c;
    --button-text: #f4f4f4;
  }
  * { margin: 0; padding: 0; box-sizing: border-box; }
  html, body {
    width: 1200px;
    height: 620px;
    overflow: hidden;
    background: var(--bg);
  }
  .landing {
    position: relative;
    width: 1200px;
    height: 620px;
    background: var(--bg);
  }
  .corner-ornament {
    position: absolute;
    width: 74px;
    height: 74px;
    background: var(--ornament);
    border-radius: 4px;
  }
  .corner-ornament--tl { top: 10px; left: 13px; }
  .corner-ornament--tr { top: 10px; right: 13px; }
  .corner-ornament--bl { bottom: 10px; left: 13px; }
  .corner-ornament--br { bottom: 10px; right: 13px; }

  .brand-mark {
    position: absolute;
    left: 520px;
    top: 133px;
    width: 160px;
    height: 160px;
  }
  .brand-name {
    position: absolute;
    left: 0;
    width: 1200px;
    top: 310px;
    text-align: center;
    font-family: "Cinzel", serif;
    font-weight: 400;
    font-size: 46px;
    letter-spacing: 4px;
    line-height: 1;
    color: var(--gold);
  }
  .brand-tagline {
    position: absolute;
    left: 0;
    width: 1200px;
    top: 363px;
    text-align: center;
    font-family: "Cinzel", serif;
    font-weight: 400;
    font-size: 17px;
    letter-spacing: 2.2px;
    line-height: 1;
    color: var(--gold);
  }
  .enter-frame {
    position: absolute;
    left: 496px;
    top: 488px;
    width: 208px;
    height: 48px;
    background: var(--button-frame);
    border-radius: 6px;
    padding: 5px;
  }
  .enter-button {
    display: flex;
    align-items: center;
    justify-content: center;
    width: 100%;
    height: 100%;
    background: linear-gradient(var(--button-top), var(--button-bottom));
    border-radius: 4px;
    font-family: "Open Sans", sans-serif;
    font-weight: 600;
    font-size: 14px;
    color: var(--button-text);
    text-decoration: none;
  }
</style>
</head>
<body>
  <main class="landing">
    <div class="corner-ornament corner-ornament--tl" role="img" aria-label="Decorative scroll corner ornament"></div>
    <div class="corner-ornament corner-ornament--tr" role="img" aria-label="Decorative scroll corner ornament"></div>
    <div class="corner-ornament corner-ornament--bl" role="img" aria-label="Decorative scroll corner ornament"></div>
    <div class="corner-ornament corner-ornament--br" role="img" aria-label="Decorative scroll corner ornament"></div>

    <svg class="brand-mark" viewBox="0 0 160 160" aria-hidden="true">
      <circle cx="80" cy="80" r="66" fill="none" stroke="#d6b768" stroke-width="3"/>
    </svg>

    <h1 class="brand-name">ELENA MARLOWE</h1>
    <p class="brand-tagline">LUXURY WEDDING &amp; EVENT CONSULTANTS</p>

    <div class="enter-frame">
      <a class="enter-button" href="#home">CLICK TO ENTER</a>
    </div>
  </main>
</body>
</html>
```